Small Business Broker Business Card Design

A business card design for a small business brokerage, which is a financial service, not unlike real estate brokerage, but for small businesses such as laundromats, pizza shops, restaurants, cleaners etc. The designs should all be simple, more conservative in nature, using the colors and font of the logo. Again, think real estate Brokerage as a business context
Contact Information for Business Card
Name: Glen R. Harlow. Title: Small Business Advisor. Email: g.harlow@bayfieldcapitalworks.example. Mobile: (555) 274-3918. Office: (555) 806-2147. www.bayfieldcapitalworks.example

```html
<!DOCTYPE html>
<html lang="en">
<head>
<meta charset="utf-8">
<title>Bayfield Capital Works – Business Card</title>
<link href="https://fonts.googleapis.com/css2?family=Montserrat:wght@700;800&family=Arimo:wght@400&display=swap" rel="stylesheet">
<style>
  :root {
    --navy: #17386b;
    --green: #7dbf3a;
    --green-dark: #5f9e26;
    --green-light: #8fd04a;
    --ink: #4a4a4a;
    --white: #ffffff;
    --stage: #1b1b1b;
  }
  * { margin: 0; padding: 0; box-sizing: border-box; }
  html, body { width: 1200px; height: 963px; overflow: hidden; }
  body {
    background: var(--stage);
    display: flex;
    flex-direction: column;
    align-items: center;
    justify-content: center;
    gap: 40px;
  }
  .card {
    width: 700px;
    height: 400px;
    border-radius: 26px;
    position: relative;
    overflow: hidden;
  }

  /* Front */
  .card-front { background: var(--white); padding: 42px 48px; }
  .company-name {
    font-family: "Montserrat", sans-serif;
    font-weight: 800;
    font-size: 25px;
    letter-spacing: 1.5px;
    text-transform: uppercase;
    color: var(--navy);
    line-height: 1;
  }
  .tagline {
    font-family: "Montserrat", sans-serif;
    font-weight: 700;
    font-size: 11.5px;
    letter-spacing: 1.6px;
    text-transform: uppercase;
    color: var(--green);
    margin-top: 5px;
  }
  .person { margin-top: 40px; }
  .person-name {
    font-family: "Montserrat", sans-serif;
    font-weight: 800;
    font-size: 30px;
    letter-spacing: 1px;
    text-transform: uppercase;
    color: var(--navy);
    line-height: 1;
  }
  .person-title {
    font-family: "Arimo", sans-serif;
    font-size: 19px;
    color: var(--green);
    margin-top: 4px;
  }
  .contact-list { list-style: none; margin-top: 30px; }
  .contact-item {
    display: flex;
    align-items: center;
    gap: 10px;
    font-family: "Arimo", sans-serif;
    font-size: 17px;
    color: var(--ink);
    line-height: 1.55;
  }
  .contact-icon { width: 16px; height: 16px; flex: none; }

  /* Back */
  .card-back {
    background: var(--green);
    display: flex;
    align-items: center;
    justify-content: center;
  }
  .back-texture {
    position: absolute;
    inset: 0;
    background: linear-gradient(135deg, var(--green-light) 0%, var(--green) 50%, var(--green-dark) 100%);
  }
  .back-brand {
    position: relative;
    display: flex;
    align-items: center;
    gap: 18px;
    color: var(--white);
  }
  .brand-square { width: 46px; height: 46px; background: var(--white); flex: none; }
  .back-brand .company-name, .back-brand .tagline { color: var(--white); }
</style>
</head>
<body>

<section class="card card-front">
  <div class="company-name">Bayfield Capital Works, Inc</div>
  <div class="tagline">Confidently buy or sell a local business today</div>

  <div class="person">
    <div class="person-name">Glen R. Harlow</div>
    <div class="person-title">Small Business Advisor</div>
  </div>

  <ul class="contact-list">
    <li class="contact-item">
      <svg class="contact-icon" viewBox="0 0 16 16" aria-hidden="true"><path fill="var(--green)" d="M3.6 1.5l2.3 2.6-1.3 1.6c.9 2 2.5 3.6 4.5 4.6l1.6-1.3 2.6 2.3-1.4 2.2C7.3 13.3 2.7 8.7 1.5 2.9z"/></svg>
      <span>(555) 806-2147</span>
    </li>
    <li class="contact-item">
      <svg class="contact-icon" viewBox="0 0 16 16" aria-hidden="true"><rect x="4" y="1" width="8" height="14" rx="1.5" fill="none" stroke="var(--green)" stroke-width="1.6"/><circle cx="8" cy="12.3" r="0.9" fill="var(--green)"/></svg>
      <span>(555) 274-3918</span>
    </li>
    <li class="contact-item">
      <svg class="contact-icon" viewBox="0 0 16 16" aria-hidden="true"><rect x="1" y="3" width="14" height="10" rx="1" fill="none" stroke="var(--green)" stroke-width="1.6"/><path d="M1.5 3.8L8 9l6.5-5.2" fill="none" stroke="var(--green)" stroke-width="1.6"/></svg>
      <span>g.harlow@bayfieldcapitalworks.example</span>
    </li>
    <li class="contact-item">
      <svg class="contact-icon" viewBox="0 0 16 16" aria-hidden="true"><circle cx="8" cy="8" r="6.8" fill="none" stroke="var(--green)" stroke-width="1.5"/><ellipse cx="8" cy="8" rx="3" ry="6.8" fill="none" stroke="var(--green)" stroke-width="1.3"/><path d="M1.5 8h13M2.6 4.6h10.8M2.6 11.4h10.8" stroke="var(--green)" stroke-width="1.2"/></svg>
      <span>www.bayfieldcapitalworks.example</span>
    </li>
  </ul>
</section>

<section class="card card-back">
  <div class="back-texture" role="img" aria-label="Embossed repeating brand pattern across the green card back"></div>
  <div class="back-brand">
    <div class="brand-square" aria-hidden="true"></div>
    <div>
      <div class="company-name">Bayfield Capital Works, Inc</div>
      <div class="tagline">Confidently buy or sell a local business today</div>
    </div>
  </div>
</section>

</body>
</html>
```